SavannaPlate Web Page Templates

I need two templates designed for a wholesale food/catering business, one template for the home page and the other for detail pages. The overall template should be a simple, clean and clear design. I have provided the existing logo to which the templates should directly relate.
SavannaPlate supplies food based upon traditional Ghanian recipes to a number of stores across Canberra. In addition, SavannaPlate offers catering for public and private functions across the Canberra region.
The colours in the logo represent the national colours of Ghana (yellow, green, red and black) and the website content will also include traditional Ghanian Kente patterns which will add further colour elements to the site. On this basis, the template design needs to be fairly sparse so as not to compete with the colourful content of the website detail pages.
There is no requirement for specific pages to be designed, as these will be handled in the CMS implementation.
The information provided in the Word document is only designed to provide a sense of the intended content of the website, not as a requirement for specific pages to be produced.

Target Market(s)

Retail/Wholesale food

Number of Pages Required

2 page

Font styles to use
Serif

Colors

Designer to choose colors to be used in the design.

Requirements
Must have
• Template must accommodate a responsive design
• The logo provided will form the cornerstone of the design
Nice to have
• There
Should not have
• Please do not solicit for extra work or for alternative logo design.

```html
<!DOCTYPE html>
<html lang="en">
<head>
<meta charset="utf-8">
<title>SavannaPlate — Home</title>
<link href="https://fonts.googleapis.com/css2?family=Lora:wght@400;500;600;700&display=swap" rel="stylesheet">
<style>
:root{
  --ink:#111;
  --text:#222;
  --red:#e0201c;
  --gold:#b8922e;
  --line:#d8d8d8;
  --dark:#141414;
  --white:#fff;
  --grey:#888;
  --orange:#e8782b;
}
*{box-sizing:border-box;margin:0;padding:0}
html,body{width:1200px;height:3137px;overflow:hidden}
body{position:relative;background:var(--white);font-family:'Lora',Georgia,serif;color:var(--text)}
.abs{position:absolute}
.center{left:0;width:1200px;text-align:center}

/* header */
.brand{top:48px;font-size:38px;font-weight:600;color:var(--gold);letter-spacing:1px}
.header-rule{top:118px;left:60px;width:1080px;height:1px;background:var(--line)}
.main-nav a{position:absolute;top:147px;font-size:14px;font-weight:700;color:var(--ink);text-decoration:none}
.main-nav a.active{color:var(--red)}
.nav-underline{top:191px;left:77px;width:57px;height:3px;background:var(--red)}
.cart{top:146px;left:1036px;font-size:14px;font-weight:700;color:var(--ink);display:flex;gap:8px;align-items:center}
.social{left:1149px;width:40px;height:40px;border-radius:50%}

/* hero */
.hero{top:195px;left:0;width:1200px;height:566px;background:radial-gradient(ellipse at 55% 40%,#d9662d 0%,#b3421d 40%,#6b2a16 80%,#3a1a10 100%)}
.hero-title{top:390px;font-size:74px;font-weight:700;color:var(--white)}
.hero-svg{top:660px;left:0}

/* intro */
.intro-title{top:826px;font-size:49px;font-weight:700;color:var(--ink)}
.intro-text{top:908px;left:128px;width:944px;text-align:center;font-size:13.5px;line-height:22px;color:var(--text)}
.tagline{top:1008px;font-size:33px;font-weight:600;color:var(--red)}

/* shops */
.shops-bg{top:1077px;left:0}
.shops-title{top:1220px;font-size:43px;font-weight:700;line-height:49px;color:var(--white)}
.shop{width:301px;height:134px;border:1px solid var(--gold);padding:12px}
.shop-inner{width:100%;height:100%;background:var(--white);display:flex;align-items:center;justify-content:center;gap:10px;font-size:24px;font-weight:700;color:var(--ink)}
.shop-dot{width:22px;height:22px;border-radius:50%;background:var(--red)}

/* catering */
.catering-text{top:1876px;left:200px;width:800px;text-align:center;font-size:16.5px;line-height:22px;color:#333}
.dish{top:1959px;width:247px;height:171px}
.dish-caption{top:2140px;width:247px;text-align:center;font-size:16.5px;font-weight:600;color:#222}
.dot{top:2216px;width:11px;height:11px;border-radius:50%;background:var(--grey)}
.dot.on{background:var(--orange)}

/* offer */
.offer{top:2306px;left:136px;width:926px;height:253px;background:linear-gradient(180deg,#2b2624 0%,#3a2521 55%,#6b1a14 100%);text-align:center;color:var(--white)}
.offer h2{margin-top:46px;font-size:51px;font-weight:700;line-height:56px}
.offer p{font-size:25px;line-height:29px;margin-top:2px}

/* contact */
.contact-icon{top:2602px;left:588px}
.contact-title{top:2638px;font-size:40px;font-weight:700;color:var(--ink)}
.contact-line{top:2696px;font-size:25px;color:#222}

/* footer */
.footer{top:2790px;left:0;width:1200px;height:347px}
.footer-brand{top:2860px;font-size:36px;font-weight:600;color:var(--gold);letter-spacing:1px}
.footer-nav a{position:absolute;top:2945px;font-size:14px;font-weight:700;color:var(--white);text-decoration:none}
.card{top:3001px;width:44px;height:30px;border-radius:4px}
.copyright{top:3058px;font-family:'Lora',Georgia,serif;font-size:13px;color:var(--white)}
</style>
</head>
<body>

<header>
  <div class="abs center brand">SavannaPlate</div>
  <div class="abs header-rule"></div>
  <nav class="main-nav">
    <a class="active" href="#" style="left:82px">Home</a>
    <a href="#" style="left:158px">About Us</a>
    <a href="#" style="left:257px">Menu</a>
    <a href="#" style="left:332px">Location</a>
    <a href="#" style="left:428px">Services</a>
    <a href="#" style="left:523px">Contact Us</a>
  </nav>
  <div class="abs nav-underline"></div>
  <div class="abs cart">
    <svg width="17" height="15" viewBox="0 0 17 15"><path d="M0 1h3l2 8h9l2-6H4.5" fill="none" stroke="#111" stroke-width="2"/><circle cx="6" cy="13" r="1.6" fill="#111"/><circle cx="13" cy="13" r="1.6" fill="#111"/></svg>
    <span>Cart : (0)</span>
  </div>
</header>

<div class="abs social" style="top:107px;background:#1b2f8c"></div>
<div class="abs social" style="top:154px;background:#2a9fe8"></div>
<div class="abs social" style="top:203px;background:#c8124f"></div>
<div class="abs social" style="top:250px;background:#e01818"></div>

<section>
  <div class="abs hero" role="img" aria-label="Plate of jollof rice with glazed chicken and fresh herbs"></div>
  <div class="abs center hero-title">SavannaPlate</div>
  <svg class="abs hero-svg" width="1200" height="102" viewBox="0 0 1200 102">
    <polygon points="0,102 0,101 740,45 1200,12 1200,102" fill="#fff"/>
    <polygon points="740,45 1200,12 1200,94" fill="var(--gold)"/>
    <polygon points="1049,44 1061,52 1061,36" fill="#fff"/>
    <polygon points="1113,44 1101,36 1101,52" fill="#fff"/>
  </svg>
</section>

<section>
  <h1 class="abs center intro-title">SavannaPlate commenced in 2004</h1>
  <p class="abs intro-text">Coming from Ghana and with a passion for cooking I realized, through school P&amp;C fundraising, that as well as enjoying my dishes, people wanted to learn more about Ghanaian food. So I started introducing pre-packaged meals at farmers' markets and food festivals to showcase Ghanaian food far and wide. They took off! People relished the exotic flavours. So why don't you give it a go?</p>
  <p class="abs center tagline">Have a taste! Enjoy!!</p>
</section>

<section>
  <svg class="abs shops-bg" width="1200" height="780" viewBox="0 0 1200 780" role="img" aria-label="Dark background of freshly made food dishes">
    <defs>
      <radialGradient id="shopsTone" cx="50%" cy="45%" r="70%">
        <stop offset="0" stop-color="#4a3428"/>
        <stop offset="1" stop-color="#241a15"/>
      </radialGradient>
    </defs>
    <polygon points="0,91 1200,0 1200,669 622,719 600,749 578,723 0,779" fill="url(#shopsTone)"/>
  </svg>
  <h2 class="abs center shops-title">Our beautiful freshly made food<br>is available weekly in the following shops</h2>

  <div class="abs shop" style="top:1393px;left:113px"><div class="shop-inner"><span class="shop-dot" style="background:#2a9a3a"></span>Harvest Lane Market</div></div>
  <div class="abs shop" style="top:1393px;left:450px"><div class="shop-inner">Northside Grocer</div></div>
  <div class="abs shop" style="top:1393px;left:786px"><div class="shop-inner"><span class="shop-dot"></span>Corner Pantry</div></div>
  <div class="abs shop" style="top:1570px;left:113px"><div class="shop-inner"><span class="shop-dot" style="background:#222"></span>Ember Goodfoods</div></div>
  <div class="abs shop" style="top:1570px;left:450px"><div class="shop-inner" style="font-size:34px">Kestrel</div></div>
  <div class="abs shop" style="top:1570px;left:786px"><div class="shop-inner" style="color:#1c3f94"><span class="shop-dot" style="background:#f0a020"></span>Lakeside Hotel</div></div>
</section>

<section>
  <p class="abs catering-text">We also cater for functions, either cocktail or sit-down dining, where we offer special dishes such as jollof rice, gari fortor, etc.</p>

  <div class="abs dish" style="left:91px;background:linear-gradient(135deg,#3a2a24,#e8785a 45%,#f2e6dc 80%)" role="img" aria-label="Cuisine dish"></div>
  <div class="abs dish" style="left:348px;background:radial-gradient(circle at 50% 45%,#b07a3a,#3a2f24 70%)" role="img" aria-label="Roast chicken special"></div>
  <div class="abs dish" style="left:605px;background:radial-gradient(circle at 50% 50%,#d8c89a,#c84a30 45%,#2a2624 75%)" role="img" aria-label="Prawn pasta special"></div>
  <div class="abs dish" style="left:862px;background:radial-gradient(circle at 45% 55%,#e0502a,#8a2a1a 60%,#4a2a20)" role="img" aria-label="Roasted tomato dish"></div>

  <p class="abs dish-caption" style="left:91px">Cuisine</p>
  <p class="abs dish-caption" style="left:348px">Chicken Special Cuisine</p>
  <p class="abs dish-caption" style="left:605px">Prawn Specials</p>
  <p class="abs dish-caption" style="left:862px">Fantastic Food</p>

  <span class="abs dot" style="left:551px"></span>
  <span class="abs dot on" style="left:580px"></span>
  <span class="abs dot" style="left:609px"></span>
  <span class="abs dot" style="left:638px"></span>
</section>

<section class="abs offer" role="img" aria-label="Bowl of sweet chilli sauce on a dark table">
  <h2>We also offer</h2>
  <p>Black-eyed beans snacks served with our home made sweet chilli<br>sauce or traditional Ghanaian chilli sauce.<br>Coconut sweet.</p>
</section>

<section>
  <svg class="abs contact-icon" width="24" height="18" viewBox="0 0 24 18"><rect x="1" y="1" width="22" height="16" rx="2" fill="none" stroke="#111" stroke-width="2"/><path d="M1 3l11 8 11-8" fill="none" stroke="#111" stroke-width="2"/></svg>
  <h2 class="abs center contact-title">Contact Us</h2>
  <p class="abs center contact-line">www.savannaplate.com.au or hello@savannaplate-mail.com</p>
</section>

<footer>
  <svg class="abs footer" width="1200" height="347" viewBox="0 0 1200 347">
    <defs>
      <pattern id="zigzag" width="12" height="10" patternUnits="userSpaceOnUse">
        <polygon points="0,10 6,2 12,10" fill="var(--dark)"/>
      </pattern>
    </defs>
    <rect x="0" y="0" width="1200" height="10" fill="url(#zigzag)"/>
    <rect x="0" y="10" width="1200" height="337" fill="var(--dark)"/>
  </svg>
  <div class="abs center footer-brand">SavannaPlate</div>
  <nav class="footer-nav">
    <a href="#" style="left:340px">Home</a>
    <a href="#" style="left:417px">About Us</a>
    <a href="#" style="left:515px">Menu</a>
    <a href="#" style="left:591px">Location</a>
    <a href="#" style="left:687px">Services</a>
    <a href="#" style="left:781px">Contact Us</a>
  </nav>
  <span class="abs card" style="left:475px;background:#2a3a9a"></span>
  <span class="abs card" style="left:527px;background:#2a58a8"></span>
  <span class="abs card" style="left:579px;background:#2a7fd0"></span>
  <span class="abs card" style="left:631px;background:#f08a1a"></span>
  <span class="abs card" style="left:683px;background:#333"></span>
  <p class="abs center copyright">© 2019 &nbsp;| www.companyname.com</p>
</footer>

</body>
</html>
```